Redesign website for small print company

Vindurgata is a small printing company in Iceland mainly servicing Students, schools, etc. We are also doing all kind of other jobs, like business cards, book printing, brochure printing etc. We are also selling books online.
Our website is: www.vindurgata.is
What we are looking for is:
- Web Design (Uncoded - PSD layout only)
- Mobile friendly design, using our current color scheme: Red, green, yellow and light gray.
- Clean simple design
- Simple, light and easy to use.
- More menu Items/drop down
Industry/Entity Type
Digital Printing
Number of Pages Required
5+ page
Requirements
Must have
- Easy navigation
- Designed for mobile
- Current color scheme (see logo)
Nice to have
- Icon based products

```html
<!DOCTYPE html>
<html lang="en">
<head>
<meta charset="utf-8">
<title>Vindurgata – Printing for Students and Schools</title>
<link rel="stylesheet" href="https://fonts.googleapis.com/css2?family=Poppins:wght@500;600;700;800&family=Open+Sans:wght@400;600&display=swap">
<style>
:root{
  --red:#e3232a;
  --red-dark:#c8151c;
  --green:#0f4f27;
  --green-dark:#0a3a1c;
  --yellow:#f2c100;
  --grey-light:#f2f2f2;
  --ink:#222;
  --muted:#555;
  --footer:#262626;
  --white:#fff;
}
*{box-sizing:border-box;margin:0;padding:0}
html,body{width:1200px;height:3956px;overflow:hidden}
body{font-family:"Open Sans",Arial,sans-serif;color:var(--ink);background:var(--white);position:relative}
h1,h2,h3,.brand,.nav{font-family:"Poppins",Arial,sans-serif}
.abs{position:absolute}

/* hero */
.hero{position:absolute;left:0;top:0;width:1200px;height:717px;
  background:linear-gradient(180deg,#3a3d42 0%,#5b5e63 45%,#7b7c7f 75%,#4a4b4e 100%)}
.hero-shade{position:absolute;inset:0;background:rgba(0,0,0,.25)}
.topbar{position:absolute;top:14px;left:82px;right:82px;height:20px;color:#fff;font-size:12px;display:flex;gap:34px}
.topbar .right{margin-left:auto;display:flex;gap:22px}
.header{position:absolute;top:62px;left:82px;right:82px;height:56px;display:flex;align-items:center}
.brand{color:#fff;font-weight:700;font-size:30px;letter-spacing:.5px;display:flex;align-items:center;gap:12px}
.brand .mark{width:40px;height:40px;background:var(--yellow)}
.nav{margin-left:auto;display:flex;gap:34px;color:#fff;font-size:15px;font-weight:500;align-items:center}
.nav .active{color:var(--red)}
.nav .dot{width:16px;height:16px;border-radius:50%;background:#fff}
.hero-title{position:absolute;left:278px;top:262px;color:#fff;font-family:"Poppins",sans-serif;font-weight:800;font-size:86px;letter-spacing:1px}
.hero-sub{position:absolute;left:324px;top:360px;color:#fff;font-size:22px;line-height:44px;width:400px}
.follow{position:absolute;left:40px;top:290px;width:16px;display:flex;flex-direction:column;gap:20px;align-items:center}
.follow span{width:12px;height:12px;border-radius:50%;background:#fff}
.follow .label{width:auto;height:auto;background:none;border-radius:0;color:#fff;font-size:13px;writing-mode:vertical-rl;transform:rotate(180deg);margin-top:10px}
.slider-dots{position:absolute;left:1145px;top:388px;display:flex;flex-direction:column;gap:14px;align-items:center}
.slider-dots span{width:12px;height:12px;border-radius:50%;background:#fff}
.slider-dots .on{width:22px;height:22px;border:3px solid #fff;background:transparent;position:relative}
.slider-dots .on::after{content:"";position:absolute;inset:4px;border-radius:50%;background:#fff}

/* dropdown */
.dropdown{position:absolute;left:490px;top:137px;width:634px;height:380px;background:#fff;box-shadow:0 6px 20px rgba(0,0,0,.25);
  display:grid;grid-template-columns:repeat(3,182px);grid-template-rows:repeat(2,170px);gap:14px 30px;padding:16px 24px}
.dd-item{text-align:center}
.dd-thumb{height:138px;background:linear-gradient(135deg,#e7e7e7,#bdbdbd)}
.dd-item p{color:var(--red);font-family:"Poppins",sans-serif;font-size:14px;font-weight:500;margin-top:8px;text-transform:uppercase}

/* features */
.features{position:absolute;top:717px;left:0;width:1200px;height:377px;display:flex;justify-content:center;gap:128px;padding-top:68px}
.feature{width:220px;text-align:center}
.feature .ico{width:76px;height:76px;border-radius:50%;background:var(--red);margin:0 auto 20px;display:flex;align-items:center;justify-content:center}
.feature h3{font-size:17px;font-weight:600;color:var(--green);margin-bottom:16px}
.feature p{font-size:14px;line-height:27px;color:var(--muted)}

/* products */
.products{position:absolute;top:1094px;left:0;width:1200px;height:520px;background:linear-gradient(180deg,var(--green) 0%,#1a5c33 60%,var(--green-dark) 100%);text-align:center;color:#fff}
.products h2{font-size:38px;font-weight:700;margin-top:56px}
.products .lead{width:900px;margin:12px auto 0;font-size:15px;line-height:29px;color:#e7efe9}
.cards{position:absolute;top:198px;left:100px;display:flex;gap:14px}
.card{width:321px;height:258px;background:#fff;color:var(--ink);padding-top:26px}
.card .cico{width:90px;height:70px;margin:0 auto}
.card h3{color:var(--red);font-size:19px;font-weight:500;margin-top:14px;text-transform:uppercase}
.card p{font-size:13px;line-height:20px;color:var(--muted);width:230px;margin:10px auto 0}
.card .more{color:var(--yellow);font-size:13px;font-weight:600;margin-top:10px;display:block}
.arrow{position:absolute;top:310px;width:32px;height:32px;border-radius:50%;background:var(--green-dark);display:flex;align-items:center;justify-content:center}

/* welcome */
.welcome{position:absolute;top:1614px;left:0;width:1200px;height:390px;text-align:center}
.welcome .tint{position:absolute;left:488px;top:60px;width:228px;height:290px;background:linear-gradient(180deg,rgba(242,193,0,.12),rgba(227,35,42,.12))}
.welcome h2{position:relative;color:var(--green);font-size:35px;font-weight:700;margin-top:70px}
.welcome p{position:relative;width:1000px;margin:22px auto 0;font-size:17px;line-height:32px;color:#333}

/* gallery */
.gallery{position:absolute;top:2004px;left:0;width:1200px;height:839px;text-align:center}
.gallery h2{color:var(--red);font-size:36px;font-weight:700;margin-top:58px}
.filters{display:flex;justify-content:center;gap:20px;margin-top:34px}
.filters span{background:var(--red);color:#fff;font-size:14px;font-weight:600;padding:8px 14px}
.filters .on{background:var(--green)}
.grid{position:absolute;top:251px;left:100px;display:grid;grid-template-columns:repeat(3,322px);grid-template-rows:repeat(2,258px);gap:11px 14px}
.grid div{box-shadow:0 2px 6px rgba(0,0,0,.2)}

/* contact */
.contact{position:absolute;top:2843px;left:0;width:1200px;height:712px;background:linear-gradient(160deg,#e6373d 0%,var(--red) 50%,var(--red-dark) 100%);text-align:center;color:#fff}
.contact h2{font-size:37px;font-weight:700;margin-top:42px}
.contact .lead{width:720px;margin:12px auto 0;font-size:15px;line-height:29px}
.contact-photo{position:absolute;left:543px;top:190px;width:575px;height:464px;background:linear-gradient(135deg,#7a8a98,#b9b0a5 50%,#5b4a44)}
.form{position:absolute;left:84px;top:221px;width:528px;height:470px;background:#fff;text-align:left;padding:34px 40px}
.form h3{color:var(--green);font-size:25px;font-weight:700}
.fields{display:grid;grid-template-columns:220px 220px;gap:18px 18px;margin-top:26px}
.field{height:48px;border:1px solid #ccc;box-shadow:inset 0 1px 4px rgba(0,0,0,.1);color:#888;font-size:13px;padding:14px}
.field.msg{grid-column:1/3;height:90px}
.submit{display:inline-block;margin-top:24px;background:var(--red);color:#fff;font-weight:600;font-size:16px;padding:10px 40px;border-radius:24px}

/* footer */
.footer{position:absolute;top:3555px;left:0;width:1200px;height:401px;background:linear-gradient(180deg,#333,#1c1c1c);color:#fff;text-align:center}
.footer .brand{justify-content:center;font-size:64px;margin-top:52px;gap:20px}
.footer .brand .mark{width:88px;height:88px}
.info{display:flex;justify-content:center;gap:44px;margin-top:36px;font-size:15px}
.socials{display:flex;justify-content:center;gap:20px;margin-top:30px}
.socials span{width:42px;height:42px;border-radius:50%;background:#2a8a3a}
.links{margin-top:24px;font-size:15px}
.copy{margin-top:26px;font-size:14px;font-weight:600}
</style>
</head>
<body>

<section class="hero">
  <div class="hero-shade" role="img" aria-label="Print shop floor with large printing machines"></div>
  <div class="topbar">
    <span>☎ 555 0142</span><span>◷ Mon - Fri: 9-17</span><span>✉ verk@vindurgata.is</span>
    <div class="right"><span>login</span><span>Register</span><span>English ▾</span></div>
  </div>
  <header class="header">
    <div class="brand"><span class="mark"></span>VINDURGATA</div>
    <nav class="nav">
      <span>Home</span><span class="active">Services</span><span>Job submit</span><span>About us</span><span class="dot"></span><span class="dot"></span>
    </nav>
  </header>
  <h1 class="hero-title">VINDURGATA</h1>
  <p class="hero-sub">Sed ut perspiciatis unde omnis iste voluptate accusantium</p>
  <div class="follow"><span></span><span></span><span></span><span></span><span class="label">Follow us</span></div>
  <div class="slider-dots"><span></span><span class="on"></span><span></span></div>

  <div class="dropdown">
    <div class="dd-item"><div class="dd-thumb" role="img" aria-label="Printed essays"></div><p>Essays</p></div>
    <div class="dd-item"><div class="dd-thumb" role="img" aria-label="Stack of business cards"></div><p>Business cards</p></div>
    <div class="dd-item"><div class="dd-thumb" role="img" aria-label="Folded leaflets"></div><p>Leaflets</p></div>
    <div class="dd-item"><div class="dd-thumb" role="img" aria-label="Printed books"></div><p>Bookprinting</p></div>
    <div class="dd-item"><div class="dd-thumb" role="img" aria-label="Rolled posters"></div><p>Posters</p></div>
    <div class="dd-item"><div class="dd-thumb" role="img" aria-label="Printed textbooks"></div><p>Textbooks</p></div>
  </div>
</section>

<section class="features">
  <div class="feature">
    <div class="ico"><svg width="36" height="36" viewBox="0 0 36 36"><path d="M7 19l7 7 15-16" fill="none" stroke="#fff" stroke-width="4"/></svg></div>
    <h3>QUALITY PRINTING</h3>
    <p>Neque porro quisquam qui dood lorem ipsum quia dolor sit amet consec tetur adipisci velit consec tet.</p>
  </div>
  <div class="feature">
    <div class="ico"><svg width="38" height="38" viewBox="0 0 38 38"><circle cx="19" cy="20" r="13" fill="none" stroke="#fff" stroke-width="3"/><path d="M19 12v8l6 4" fill="none" stroke="#fff" stroke-width="3"/></svg></div>
    <h3>TIMELY DELIVERY</h3>
    <p>Neque porro quisquam qui dood lorem ipsum quia dolor sit amet consec tetur adipisci velit consec tet.</p>
  </div>
  <div class="feature">
    <div class="ico"><svg width="38" height="38" viewBox="0 0 38 38"><path d="M8 30C8 14 18 7 31 7c0 14-8 23-23 23z" fill="#fff"/><path d="M8 30L24 14" stroke="var(--red)" stroke-width="2"/></svg></div>
    <h3>ECO-MINDED</h3>
    <p>Neque porro quisquam qui dood lorem ipsum quia dolor sit amet consec tetur adipisci velit consec tet.</p>
  </div>
</section>

<section class="products">
  <h2>PRODUCT LIST</h2>
  <p class="lead">Sed ut perspiciatis unde omnis iste natus error sit voluptatem accusantium doloremque laudantium, totam rem aperiam, eaque ipsa quae ab illo inventore veritatis et quasi architecto beatae vitae dicta sunt explicabo.</p>
  <div class="arrow" style="left:53px"><svg width="12" height="12" viewBox="0 0 12 12"><path d="M8 1L3 6l5 5" fill="none" stroke="#fff" stroke-width="2"/></svg></div>
  <div class="arrow" style="left:1110px"><svg width="12" height="12" viewBox="0 0 12 12"><path d="M4 1l5 5-5 5" fill="none" stroke="#fff" stroke-width="2"/></svg></div>
  <div class="cards">
    <div class="card">
      <svg class="cico" viewBox="0 0 90 70"><rect x="2" y="2" width="86" height="66" rx="6" fill="none" stroke="var(--red)" stroke-width="4"/><circle cx="28" cy="28" r="9" fill="none" stroke="var(--red)" stroke-width="4"/><path d="M14 54c2-10 26-10 28 0" fill="none" stroke="var(--red)" stroke-width="4"/><path d="M52 24h26M52 36h26M52 48h18" stroke="var(--red)" stroke-width="4"/></svg>
      <h3>Business cards</h3>
      <p>At vero eos et accusamus et iusto odio dignissimos ducimus qui blanditiis</p>
      <span class="more">Read More</span>
    </div>
    <div class="card">
      <svg class="cico" viewBox="0 0 90 70"><path d="M30 4l-22 12 8 14 8-4v40h42V26l8 4 8-14L60 4c-4 8-26 8-30 0z" fill="none" stroke="var(--red)" stroke-width="4" stroke-linejoin="round"/><rect x="36" y="28" width="18" height="18" fill="none" stroke="var(--red)" stroke-width="3"/></svg>
      <h3>Posters</h3>
      <p>At vero eos et accusamus et iusto odio dignissimos ducimus qui blanditiis</p>
      <span class="more">Read More</span>
    </div>
    <div class="card">
      <svg class="cico" viewBox="0 0 90 70"><path d="M4 8h26l15 8 15-8h26v56H60l-15 4-15-4H4z" fill="none" stroke="var(--red)" stroke-width="4" stroke-linejoin="round"/><path d="M45 16v50M12 22h22M12 32h22M12 42h22M56 22h22M56 32h22M56 42h22" stroke="var(--red)" stroke-width="3"/></svg>
      <h3>Leaflets</h3>
      <p>At vero eos et accusamus et iusto odio dignissimos ducimus qui blanditiis</p>
      <span class="more">Read More</span>
    </div>
  </div>
</section>

<section class="welcome">
  <div class="tint"></div>
  <h2>WELCOME TO UNIVERSITY</h2>
  <p>University education is a company located in the campus, which has specialized in the service of school staff, as well as providing general public printing. Higher education publishes seminars and first-class textbooks for courses, prints theses for lesson, as well as working on an unprecedented number of smaller pieces for students, teachers and organizations.These include brochures, reports, questionnaires, business cards, books, OCR scanning and more.</p>
  <p>Higher education is a tailored print shop. The Heron is the official eco-label of the Nordic countries, which has created a foothold in this country and is known among consumers.</p>
</section>

<section class="gallery">
  <h2>GALLERY</h2>
  <div class="filters">
    <span class="on">All Projects</span><span>Leaflets &amp; Flyers</span><span>Stationary</span><span>3d Products</span><span>Presentation</span><span>Brochure</span><span>Ecommerce</span>
  </div>
  <div class="grid">
    <div role="img" aria-label="Spread of folded brochures" style="background:linear-gradient(135deg,#d9dde2,#6d7e92 60%,#3f4b5c)"></div>
    <div role="img" aria-label="Colourful printed book covers" style="background:linear-gradient(135deg,#f0d24a,#e0552f 50%,#3a6fb0)"></div>
    <div role="img" aria-label="Printed textbook cover with pink title" style="background:linear-gradient(135deg,#f4f1ea,#e9e4d5 55%,#d23a84)"></div>
    <div role="img" aria-label="Letterhead and envelope stationery" style="background:linear-gradient(135deg,#f3f3f3,#cfd3da)"></div>
    <div role="img" aria-label="Bound thesis cover" style="background:linear-gradient(135deg,#f5f5f5,#c9c9c9)"></div>
    <div role="img" aria-label="Stack of white paper with green arrow" style="background:linear-gradient(135deg,#eeeeee,#cdd3cd 70%,#8fc54a)"></div>
  </div>
</section>

<section class="contact">
  <h2>CONTACT US</h2>
  <p class="lead">At vero eos et accusamus et iusto odio dignissimos ducimus qui blanditiis praesentium voluptatum deleniti atque corrupti quos dolores et</p>
  <div class="contact-photo" role="img" aria-label="Two print shop staff checking a job at a computer"></div>
  <div class="form">
    <h3>GET IN TOUCH</h3>
    <div class="fields">
      <div class="field">Name</div><div class="field">Email</div>
      <div class="field">Phone Number</div><div class="field">Subject</div>
      <div class="field msg">Message</div>
    </div>
    <span class="submit">Submit</span>
  </div>
</section>

<footer class="footer">
  <div class="brand"><span class="mark"></span>VINDURGATA</div>
  <div class="info">
    <span>➤ 12 Fjarðargata Reykjavík</span><span>☎ Phone: +555 0142</span><span>✉ Email: verk@vindurgata.is</span>
  </div>
  <div class="socials"><span></span><span></span><span></span><span></span><span></span></div>
  <p class="links">Home &nbsp;|&nbsp; Our Services &nbsp;|&nbsp; Job Submit &nbsp;|&nbsp; About us</p>
  <p class="copy">Copyright © 2018, All Rights Reserved.</p>
</footer>

</body>
</html>
```